QHX Compliant Dietary Supplement Label for Nutritional Company

We are in need of a label for our line of 20+ dietary supplements that are specifically formulated to balance body chemistry and match the biochemical individuality of our users based on hair tissue mineral analysis.

We have a line of approximately 20 different dietary supplements that will require use of new label in both a small (90 capsule) and large (180 capsule) size. We will start with the initial label in which Product name, Supplement Facts, and Ingredient list will need to be modified for each particular product thereafter.

The label will be placed on a transparent blue bottle with the color of lid being decided after label design. We are open to a transparent light amber bottle with black lid but blue is our preference.

We would like the majority of the label to be blue. Solid blue, fading of blue to darker blue/black, or subtle background designs are welcome with involvement of white and hints of orange. We do not want pictorial images on the label.

Label size:
Small bottle (120cc): Label size ~ 2.25” x 5.875”
Large bottle (200cc): Label size ~ 2.75” x 7.625”

Front:
-Logo near top of label with product name and description in middle and capsule count near the bottom

Right Side:
-Supplement Facts: See current product image below in brief
-Ingredient list: See current product image below in brief
-Manufactured for: See image below (This is on the left side of our current bottle and would like it moved to the bottom of the right side)

Left side:
-Suggested use: See current product image below in brief
-Leave room for possible warning statement
-Leave room for possible lot number printing
-Keep out of the reach of children.

The first files below are our current supplement label with product information. This information is what is needed on the label and will likely need some adjustments as we are updating our line of supplements and changes in QHX requirements.

The following files are the logo files and color palette.

The remaining files are some designs we came across for inspiration.

Thank you.

Target Market(s)

Health Care Profressionals

Industry/Entity Type

Health Care and Nutrition

Requirements
Nice to have
• Product name needs to be on same line in all one color
Should not have
• Pictorial Images

```html
<!DOCTYPE html>
<html lang="en">
<head>
<meta charset="utf-8">
<title>Adreva-Core Label</title>
<link rel="stylesheet" href="https://fonts.googleapis.com/css2?family=Montserrat:wght@300;400;600&family=Saira+Condensed:ital,wght@1,800&family=Lato:wght@400;700;900&display=swap">
<style>
  :root {
    --blue: #3443a6;
    --blue-mid: #2a3688;
    --navy: #151c46;
    --ink: #0f1a3d;
    --orange: #f28a2f;
    --white: #ffffff;
    --page: #ffffff;
  }
  * { box-sizing: border-box; margin: 0; padding: 0; }
  html, body { width: 1200px; height: 906px; overflow: hidden; background: var(--page); }
  .canvas { position: relative; width: 1200px; height: 906px; }

  .label {
    position: absolute; left: 50px; top: 243px; width: 1100px; height: 420px;
    background: var(--white);
    box-shadow: 3px 4px 8px rgba(0,0,0,0.25);
    overflow: hidden;
    font-family: "Montserrat", sans-serif;
  }
  .label__band {
    position: absolute; left: 0; right: 0; top: 199px; bottom: 0;
    background: linear-gradient(180deg, var(--blue) 0%, var(--blue-mid) 45%, var(--navy) 100%);
  }

  .brand {
    position: absolute; left: 360px; top: 38px; width: 200px; text-align: center;
    color: var(--blue);
  }
  .brand__mark {
    display: block; width: 22px; height: 22px; margin: 0 auto 8px;
    border-radius: 50%; background: var(--orange);
  }
  .brand__name { font-size: 27px; font-weight: 400; letter-spacing: 1px; line-height: 1; }
  .brand__sub { font-size: 10px; font-weight: 400; letter-spacing: 4px; margin-top: 4px; }

  .product-name {
    position: absolute; left: 366px; top: 128px;
    font-family: "Saira Condensed", sans-serif; font-style: italic; font-weight: 800;
    font-size: 72px; line-height: 1; color: var(--ink); letter-spacing: -0.5px;
  }
  .product-desc {
    position: absolute; left: 368px; top: 212px;
    color: var(--white); font-weight: 400; font-size: 27px; line-height: 33px; letter-spacing: 0.5px;
  }
  .count {
    position: absolute; left: 368px; top: 330px; color: var(--orange);
  }
  .count__num { font-size: 56px; font-weight: 300; line-height: 1; }
  .count__unit { font-size: 12px; font-weight: 400; letter-spacing: 0.5px; }

  .notice {
    position: absolute; left: 31px; top: 253px; width: 268px; height: 70px;
    background: var(--white); border: 2px solid var(--orange); border-radius: 5px;
    padding: 6px 12px; color: var(--blue-mid); font-size: 13.5px; line-height: 18px;
  }
  .notice strong { font-weight: 600; }
  .batch { position: absolute; left: 31px; top: 346px; width: 268px; color: var(--white); font-size: 13px; }
  .batch__row { display: flex; align-items: flex-end; height: 26px; }
  .batch__line { flex: 1; border-bottom: 1px solid rgba(255,255,255,0.8); margin-left: 4px; margin-bottom: 4px; }

  .facts {
    position: absolute; left: 800px; top: 35px; width: 271px; height: 297px;
    background: var(--white); border: 2px solid var(--blue-mid);
    padding: 4px 6px; color: var(--blue-mid); font-family: "Lato", sans-serif;
    font-size: 9.5px; line-height: 10.5px;
  }
  .facts__title { font-size: 24px; font-weight: 900; line-height: 26px; }
  .facts__serving { font-weight: 700; }
  .facts__bar { height: 6px; background: var(--blue-mid); margin: 3px 0 2px; }
  .facts__row {
    display: grid; grid-template-columns: 1fr 46px 44px; align-items: end;
    border-bottom: 1px solid var(--blue-mid); padding: 1px 0;
  }
  .facts__row span:nth-child(2), .facts__row span:nth-child(3) { text-align: right; }
  .facts__row--head { font-size: 7.5px; line-height: 8px; font-weight: 700; border-bottom: 0; }
  .facts__row--head + .facts__row { border-top: 1px solid var(--blue-mid); }
  .facts__row .indent { padding-left: 10px; display: block; }
  .facts__row:last-of-type { border-bottom: 0; }
  .facts__note { margin-top: 3px; }

  .ingredients {
    position: absolute; left: 800px; top: 336px; width: 280px;
    color: var(--white); font-family: "Lato", sans-serif; font-size: 10px; line-height: 11.5px;
  }
  .ingredients strong { font-weight: 700; }
  .ingredients p + p { margin-top: 10px; }
</style>
</head>
<body>
<main class="canvas">
  <section class="label">
    <div class="label__band"></div>

    <div class="brand">
      <span class="brand__mark"></span>
      <div class="brand__name">NORVALE</div>
      <div class="brand__sub">LABORATORIES</div>
    </div>

    <h1 class="product-name">ADREVA-CORE</h1>
    <p class="product-desc">ADRENAL<br>SUPPLEMENT</p>
    <div class="count">
      <div class="count__num">90</div>
      <div class="count__unit">CAPSULES</div>
    </div>

    <div class="notice"><strong>NOTICE:</strong> It is advisable to keep this and all supplements out of the reach of children.</div>
    <div class="batch">
      <div class="batch__row">LOT #:<span class="batch__line"></span></div>
      <div class="batch__row">EXP:<span class="batch__line"></span></div>
    </div>

    <div class="facts">
      <div class="facts__title">Supplement Facts</div>
      <div class="facts__serving">Serving Size: 1 Capsule<br>Servings Per Container 90</div>
      <div class="facts__bar"></div>
      <div class="facts__row facts__row--head"><span></span><span>Amount Per Serving</span><span>% Daily Value</span></div>
      <div class="facts__row"><span>Vitamin C (as ascorbic acid)</span><span>100 mg</span><span>111%</span></div>
      <div class="facts__row"><span>Vitamin B5<span class="indent">(as D-calcium pantothenate)</span></span><span>100 mg</span><span>2000%</span></div>
      <div class="facts__row"><span>Magnesium (as magnesium amino<span class="indent">acid chelate)</span></span><span>5 mg</span><span>1%</span></div>
      <div class="facts__row"><span>Zinc (as zinc amino acid chelate)</span><span>1 mg</span><span>9%</span></div>
      <div class="facts__row"><span>Manganese (as manganese<span class="indent">amino acid chelate)</span></span><span>1 mg</span><span>43%</span></div>
      <div class="facts__row"><span>Potassium (as potassium<span class="indent">amino acid chelate)</span></span><span>25 mg</span><span>1%</span></div>
      <div class="facts__bar"></div>
      <div class="facts__row"><span>Suprarenal (adrenal) powder (bovine)</span><span>100 mg</span><span>†</span></div>
      <div class="facts__row"><span>Liver Powder, defatted (bovine)</span><span>45 mg</span><span>†</span></div>
      <div class="facts__row"><span>Betain Hydrochloride</span><span>25 mg</span><span>†</span></div>
      <div class="facts__bar"></div>
      <div class="facts__note">† Daily Value not established</div>
    </div>

    <div class="ingredients">
      <p><strong>Other Ingredients:</strong> Hypromellose (Vegetable Capsule), Rice-Flo (Organic Rice Fiber)</p>
      <p>Distributed by: NORVALE LABORATORIES, INC.<br>Cedar Mesa, AZ 85990 USA</p>
    </div>
  </section>
</main>
</body>
</html>
```